Display wall/splashback design

We are looking at a design to suit the background display/splashback wall of our instore showroom displays needs to be in suttle colours that do not detract from the appliances attached to this wall.
Most of the rangehoods on display are of a stainless colour hence the background cannot have strong solid colours that will attract the eye of the customer away from the products .
One of the main features of our rangehoods is their silence, so something to highlites silence/quiet would be most appropiate.
Sixe is 1.8 metres in height x 6 metres in length

Target Market(s)

High end consumer, women between 25 and 50

Industry/Entity Type

Retail

Requirements
Must have
• An overall gently/quiet and enviromentally friendly look.
A background that inhances the product displayed upon it.

Should not have
• Strong or dominant images nor strong or dominant colours

```html
<!DOCTYPE html>
<html lang="en">
<head>
<meta charset="utf-8">
<title>Showroom Splashback Wall</title>
<style>
  :root {
    --sky-top: #8fc7c0;
    --sky-mid: #a3d0d3;
    --sky-low: #b2dbe1;
    --glow-yellow: #f3ec9a;
    --band-gold: #d29a0e;
    --pale-gap: #cfe6d8;
    --floor: #b9dde4;
  }
  html, body {
    margin: 0;
    padding: 0;
    width: 1200px;
    height: 444px;
    overflow: hidden;
    background: var(--sky-low);
  }
  .splashback {
    position: relative;
    width: 1200px;
    height: 444px;
    overflow: hidden;
    background:
      linear-gradient(90deg, rgba(255,255,255,0) 0%, rgba(255,255,255,0.12) 35%, rgba(255,255,255,0.05) 60%, rgba(200,230,240,0.18) 100%),
      linear-gradient(180deg, var(--sky-top) 0%, var(--sky-mid) 30%, var(--sky-low) 62%, var(--sky-low) 100%);
  }
  .splashback__wash {
    position: absolute;
    inset: 0;
    width: 100%;
    height: 100%;
  }
  .glow-band {
    position: absolute;
    left: 0;
    width: 100%;
    background: linear-gradient(180deg, rgba(243,236,154,0) 0%, var(--glow-yellow) 45%, var(--glow-yellow) 60%, rgba(243,236,154,0.2) 100%);
  }
  .glow-band--upper { top: 284px; height: 60px; }
  .glow-band--lower { top: 352px; height: 52px; }
  .gold-line {
    position: absolute;
    left: 0;
    width: 100%;
    height: 11px;
    background: var(--band-gold);
  }
  .gold-line--upper { top: 334px; }
  .gold-line--lower { top: 400px; }
  .floor-strip {
    position: absolute;
    left: 0;
    top: 411px;
    width: 100%;
    height: 33px;
    background: linear-gradient(90deg, #cfeaee 0%, var(--floor) 20%, var(--floor) 100%);
  }
  .pale-gap {
    position: absolute;
    left: 0;
    top: 345px;
    width: 100%;
    height: 10px;
    background: var(--pale-gap);
    opacity: 0.8;
  }
</style>
</head>
<body>
  <main class="splashback">
    <svg class="splashback__wash" viewBox="0 0 1200 444" preserveAspectRatio="none" aria-hidden="true">
      <defs>
        <linearGradient id="soft-streak" x1="0" y1="0" x2="1" y2="0">
          <stop offset="0" stop-color="#ffffff" stop-opacity="0"/>
          <stop offset="0.5" stop-color="#ffffff" stop-opacity="0.14"/>
          <stop offset="1" stop-color="#ffffff" stop-opacity="0"/>
        </linearGradient>
      </defs>
      <rect x="250" y="0" width="220" height="300" fill="url(#soft-streak)"/>
      <rect x="640" y="0" width="180" height="300" fill="url(#soft-streak)"/>
      <rect x="900" y="0" width="160" height="300" fill="url(#soft-streak)"/>
    </svg>
    <div class="glow-band glow-band--upper"></div>
    <div class="gold-line gold-line--upper"></div>
    <div class="pale-gap"></div>
    <div class="glow-band glow-band--lower"></div>
    <div class="gold-line gold-line--lower"></div>
    <div class="floor-strip"></div>
  </main>
</body>
</html>
```